Design a Website in Wordpress for an Australian Health Training Company in Health related courses

We require a WORDPRESS based Website (due to add on's we need to use for third party software) to replace our old site.
We offer national face to face delivery in medical reception, terminology and also administration.
The website will have around 6 pages and the ability to describe our main 6 courses (perhaps on the Courses page this may be tabs opening up to details for example?)
I have attached a previous sample of a Joomla site which was being developed (please do not feel you have to copy this - but I am just giving it as a sample - copying would be boring). But it gives an idea of look/feel and colours which may be suitable. Open to other ideas though.
I will provide some of the content, but would like the ability to finish the content myself.
Images and graphics are important. While a few medical photos re great - don't be tempted to us all pictures of doctors and nurses (although a couple would be good) - these are administrative courses so general corporate, eye catching visionary pictures of people in general are great. A medical type picture is also fine.
THE BOOKING system - will be via an ADD ON which will occur at the end of the project and is supplied by a third party software company (our student management system). This project will include up to 2 hours working with the Tech guys from the third party software to enable the ADD ON. If this ADD ON requires more time, we will pay hourly (although I do not expect it will).
Target Market(s)
Mostly a female market, many mature aged women target 25-45 yrs. Mixture of medical/health and corporate. Maybe a bit of mums returning to work and corporate inspiration.
Industry/Entity Type
It Company
Coding
Coded - Design and coding required
Number of Pages Required
5+ page
Requirements
Must have
- Wordpress
- Great graphics
- Interesting
- professional and clean
- Enquiry section (info Pak)
- Should have a University feel to it - Education
- Pages
- Home Page - About Us - Recruitment -Courses - Class Schedule - Traineeships Queensland Funding - Latest News Blog - Corporate Training- Contact us

```html
<!DOCTYPE html>
<html lang="en">
<head>
<meta charset="utf-8">
<title>Harbourline Institute of Training</title>
<link rel="stylesheet" href="https://fonts.googleapis.com/css2?family=Bitter:wght@400;500;600&family=Lato:ital,wght@0,400;0,700;1,400&family=Roboto:wght@400;500&display=swap">
<style>
:root{
  --navy:#1f2b47;
  --navy-dark:#1a2540;
  --navy-bar:#27324e;
  --orange:#e0922f;
  --orange-soft:#e49a3c;
  --ink:#2b2b2b;
  --muted:#6b6b6b;
  --grey-line:#e2e2e2;
  --pale:#f3f3f3;
  --white:#fff;
  --course-text:#8d97ad;
}
*{margin:0;padding:0;box-sizing:border-box}
html,body{width:1200px;height:3340px;overflow:hidden}
body{position:relative;font-family:"Lato",sans-serif;color:var(--ink);background:var(--white)}
section,header,footer,nav{position:absolute;left:0;width:1200px}
.serif{font-family:"Bitter",serif}

/* top bar */
.top-bar{top:0;height:56px;background:var(--navy-bar);color:#dfe3ec;font-size:12px}
.top-bar .item{position:absolute;top:21px;display:flex;align-items:center;gap:8px}
.social{position:absolute;right:74px;top:14px;display:flex;gap:6px}
.social span{width:28px;height:28px;border:2px solid #dfe3ec;border-radius:50%}

/* header */
.site-header{top:56px;height:162px}
.brand{position:absolute;left:80px;top:26px;display:flex;align-items:center;gap:14px}
.brand-mark{width:54px;height:54px;background:var(--navy)}
.brand-name{font-family:"Bitter",serif;font-size:17px;font-weight:600;color:var(--navy);line-height:1.2;text-transform:uppercase}
.cta{position:absolute;right:74px;width:154px;height:34px;border-radius:3px;color:#fff;font:500 12px "Roboto",sans-serif;display:flex;align-items:center;justify-content:center;gap:10px;letter-spacing:.5px}
.cta.enrol{top:42px;background:var(--orange)}
.cta.info{top:90px;background:var(--navy-dark)}

/* nav */
.main-nav{top:218px;height:50px;background:var(--navy);display:flex;padding-left:62px;padding-right:60px;justify-content:space-between}
.main-nav a{color:#fff;text-decoration:none;font:500 12px "Roboto",sans-serif;display:flex;align-items:center;padding:0 24px;letter-spacing:.3px}
.main-nav a.active{background:var(--orange)}

/* hero */
.hero{top:268px;height:538px;background:linear-gradient(90deg,#d4d8e5 0%,#c7cbdc 55%,#b9bdd0 100%);overflow:hidden}
.hero-photo{position:absolute;right:0;top:0;width:640px;height:538px;background:linear-gradient(160deg,#cfd2e0,#a9aec4 60%,#8f95ae)}
.hero h1{position:absolute;left:76px;top:155px;font:400 46px "Bitter",serif;color:var(--navy)}
.hero h1 em{font-style:normal;color:var(--orange)}
.hero p{position:absolute;left:76px;top:228px;width:620px;font:italic 700 19px/1.5 "Lato",sans-serif;color:var(--navy)}
.btn{display:inline-flex;align-items:center;justify-content:center;background:var(--orange);color:#fff;font:700 12px "Lato",sans-serif;letter-spacing:.6px;text-transform:uppercase;border-radius:2px}
.hero .btn{position:absolute;left:76px;top:310px;width:168px;height:42px}
.dots{position:absolute;left:565px;top:502px;display:flex;gap:16px}
.dots span{width:11px;height:11px;border-radius:50%;background:#a5aabd}
.dots span.on{background:var(--navy)}

/* titles */
.section-title{position:absolute;left:0;width:1200px;text-align:center;font:400 30px "Bitter",serif}
.section-title::after{content:"";display:block;width:56px;height:2px;background:var(--orange);margin:12px auto 0}

/* welcome */
.welcome{top:806px;height:303px}
.welcome .section-title{top:66px;color:var(--navy)}
.welcome p{position:absolute;left:90px;width:1020px;top:134px;text-align:center;font-size:13px;line-height:1.75;color:#555}
.welcome .btn{position:absolute;left:534px;top:218px;width:132px;height:38px}

/* courses */
.courses{top:1109px;height:583px;background:linear-gradient(135deg,#2a3654,#1e2a45 60%,#26324f)}
.courses .section-title{top:70px;color:#fff}
.course{position:absolute;width:320px}
.course .head{display:flex;align-items:center;gap:14px;min-height:50px}
.course h3{font:400 20px/1.2 "Bitter",serif;color:#fff}
.course p{margin-top:10px;font-size:13px;line-height:1.6;color:var(--course-text)}
.course a{display:block;margin-top:8px;color:var(--orange);font:700 12px "Lato",sans-serif;text-decoration:none}

/* why */
.why{top:1692px;height:490px}
.why .section-title{top:54px;color:var(--ink)}
.point{position:absolute;width:492px;padding-bottom:14px}
.point.line{border-bottom:1px solid var(--grey-line)}
.point h3{font:400 22px "Bitter",serif;color:var(--orange);margin-bottom:8px}
.point p{font:italic 13px/1.6 "Lato",sans-serif;color:#444}

/* enquiry */
.enquiry{top:2182px;height:330px;background:linear-gradient(180deg,#e59b3d,#dd8e2f)}
.enquiry .section-title{top:54px;color:#fff}
.enquiry .section-title::after{background:#fff}
.field{position:absolute;width:244px;height:42px;background:#fff;border-radius:2px;display:flex;align-items:center;gap:10px;padding-left:16px;font:italic 12px "Lato",sans-serif;color:#666}
.submit{position:absolute;width:244px;height:42px;background:var(--navy);color:#fff;font:700 12px "Lato",sans-serif;display:flex;align-items:center;justify-content:center;letter-spacing:.5px}

/* testimonials */
.testimonials{top:2512px;height:350px;background:var(--pale)}
.testimonials .section-title{top:60px;color:var(--ink)}
.quote{position:absolute;left:167px;top:131px;width:870px;padding:20px 34px;background:#fff;text-align:center;font:italic 13px/1.65 "Lato",sans-serif;color:#555}
.quote::after{content:"";position:absolute;left:420px;bottom:-12px;border:12px solid transparent;border-bottom:0;border-top-color:#fff}
.avatar{position:absolute;left:522px;top:230px;width:66px;height:66px;border-radius:50%;background:linear-gradient(135deg,#c9a386,#7a5a44);border:3px solid #fff}
.client{position:absolute;left:600px;top:256px;color:var(--orange);font:700 13px "Lato",sans-serif}
.arrow{position:absolute;top:256px;color:#555;font-size:14px}

/* footer */
.site-footer{top:2862px;height:478px;background:var(--navy)}
.fcol{position:absolute;top:56px;width:230px;color:#fff}
.fcol h4{font:500 20px "Roboto",sans-serif;margin-bottom:24px}
.fcol p,.fcol li{font-size:12px;line-height:1.7;color:#9aa3b8}
.fcol ul{list-style:none}
.fcol li{margin-bottom:22px}
.fcol li b{display:block;color:#fff;font-size:11px;margin-top:4px}
.fcol .tweet{font-style:italic}
.fbrand{display:flex;align-items:center;gap:10px;margin-bottom:28px}
.fbrand span{width:36px;height:36px;background:#fff}
.fbrand strong{font:600 13px/1.2 "Bitter",serif;color:#fff;text-transform:uppercase}
.fsocial{display:flex;gap:6px;margin-top:20px}
.fsocial span{width:28px;height:28px;border:2px solid #cfd4df;border-radius:50%}
.news{display:flex;margin-top:16px}
.news div{width:180px;height:36px;background:#fff;font:italic 12px "Lato",sans-serif;color:#666;display:flex;align-items:center;padding-left:14px}
.news b{width:34px;height:36px;background:var(--navy-dark);color:#fff;display:flex;align-items:center;justify-content:center;border:1px solid #3a466a}
.copyright{position:absolute;left:0;width:1200px;top:3300px;text-align:center;font-size:12px;color:#8e97ad}
</style>
</head>
<body>

<div class="top-bar" style="position:absolute;left:0;width:1200px">
  <div class="item" style="left:78px">
    <svg width="12" height="12" viewBox="0 0 12 12"><circle cx="6" cy="6" r="5" fill="none" stroke="#dfe3ec" stroke-width="1.4"/><path d="M1 6h10M6 1c2 2 2 8 0 10M6 1c-2 2-2 8 0 10" stroke="#dfe3ec" fill="none"/></svg>
    English <span style="margin-left:14px">&#9662;</span>
  </div>
  <div class="item" style="left:212px">
    <svg width="10" height="13" viewBox="0 0 10 13"><path d="M5 0a5 5 0 0 1 5 5c0 3-5 8-5 8S0 8 0 5a5 5 0 0 1 5-5z" fill="#dfe3ec"/><circle cx="5" cy="5" r="2" fill="#27324e"/></svg>
    12 Example Street, Sampletown
  </div>
  <div class="item" style="left:455px">
    <svg width="12" height="12" viewBox="0 0 12 12"><path d="M0 6h8M5 3l3 3-3 3" stroke="#dfe3ec" stroke-width="1.6" fill="none"/><path d="M7 1h4v10H7" stroke="#dfe3ec" stroke-width="1.4" fill="none"/></svg>
    Log In / Register
  </div>
  <div class="social"><span></span><span></span><span></span><span></span></div>
</div>

<header class="site-header">
  <div class="brand">
    <div class="brand-mark"></div>
    <div class="brand-name">Harbourline Institute<br>of Training</div>
  </div>
  <div class="cta enrol">
    <svg width="12" height="14" viewBox="0 0 12 14"><rect x="1" y="1" width="10" height="12" rx="5" fill="none" stroke="#fff" stroke-width="1.6"/><path d="M6 3v3" stroke="#fff" stroke-width="1.6"/></svg>
    ENROL NOW
  </div>
  <div class="cta info">
    <svg width="13" height="12" viewBox="0 0 13 12"><rect x="1" y="4" width="11" height="7" fill="#fff"/><rect x="4" y="1" width="5" height="3" fill="none" stroke="#fff" stroke-width="1.4"/></svg>
    INFO PACK
  </div>
</header>

<nav class="main-nav">
  <a class="active">HOME</a>
  <a>ABOUT US</a>
  <a>RECRUITMENT</a>
  <a>COURSES</a>
  <a>CLASS SCHEDULE</a>
  <a>TRAINEESHIPS QUEENSLAND FUNDING</a>
  <a>LATEST NEWS BLOG</a>
  <a>MORE</a>
</nav>

<section class="hero">
  <div class="hero-photo" role="img" aria-label="Photo of a smiling doctor in a white coat gesturing toward the headline"></div>
  <h1>Cources for <em>busy people</em></h1>
  <p>Harbourline is a Registered Training Organisation offering specialised Medical Administration Training in over 15 locations Australia wide.</p>
  <span class="btn">Booking Now</span>
  <div class="dots"><span class="on"></span><span></span><span></span></div>
</section>

<section class="welcome">
  <h2 class="section-title">Welcome to Our Site</h2>
  <p>Harbourline is Australia's Leading Provider of Educational, Training and Support Services for the Medical and Dental industry – enabling students to be immediately skilled and 'Job Ready' for a career in Health. Harbourline is a Registered Training Organisation offering specialised Medical Administration Training in over 15 locations Australia wide. Harbourline have trained thousands of students the required knowledge and skills to become successful health care administrators.</p>
  <span class="btn">Read More</span>
</section>

<section class="courses">
  <h2 class="section-title">List Of Cources</h2>
  <svg width="0" height="0" style="position:absolute"><defs><symbol id="tick" viewBox="0 0 32 32"><circle cx="16" cy="16" r="13.5" fill="none" stroke="#e0922f" stroke-width="3"/><path d="M10 16.5l4.5 4.5 8-9" fill="none" stroke="#e0922f" stroke-width="3.4" stroke-linecap="round" stroke-linejoin="round"/></symbol></defs></svg>

  <div class="course" style="left:76px;top:160px"><div class="head"><svg width="32" height="32"><use href="#tick"/></svg><h3>Medical Reception &amp;<br>Terminology</h3></div><p>Neque porro quisquam est qui dolorem ipsum quia dolor sit amet, consectetur, adipisci velit.</p><a>READ MORE</a></div>
  <div class="course" style="left:444px;top:160px"><div class="head"><svg width="32" height="32"><use href="#tick"/></svg><h3>Cert III Business<br>Administration</h3></div><p>Neque porro quisquam est qui dolorem ipsum quia dolor sit amet, consectetur, adipisci velit.</p><a>READ MORE</a></div>
  <div class="course" style="left:812px;top:160px"><div class="head"><svg width="32" height="32"><use href="#tick"/></svg><h3>Medical Terminology</h3></div><p>Neque porro quisquam est qui dolorem ipsum quia dolor sit amet, consectetur, adipisci velit.</p><a>READ MORE</a></div>
  <div class="course" style="left:76px;top:354px"><div class="head"><svg width="32" height="32"><use href="#tick"/></svg><h3>Keyboard &amp;<br>Typing</h3></div><p>Neque porro quisquam est qui dolorem ipsum quia dolor sit amet, consectetur, adipisci velit.</p><a>READ MORE</a></div>
  <div class="course" style="left:444px;top:354px"><div class="head"><svg width="32" height="32"><use href="#tick"/></svg><h3>Harbourline Online</h3></div><p>Neque porro quisquam est qui dolorem ipsum quia dolor sit amet, consectetur, adipisci velit.</p><a>READ MORE</a></div>
  <div class="course" style="left:812px;top:354px"><div class="head"><svg width="32" height="32"><use href="#tick"/></svg><h3>Confidentiality</h3></div><p>Neque porro quisquam est qui dolorem ipsum quia dolor sit amet, consectetur, adipisci velit.</p><a>READ MORE</a></div>
</section>

<section class="why">
  <h2 class="section-title">Why Harbourline Institute?</h2>
  <div class="point line" style="left:76px;top:130px"><h3>Quality</h3><p>Harbourline delivery quality, effective training facilitated by industry leaders. Just ask our students who rate us on average of 4.7 out of 5.</p></div>
  <div class="point line" style="left:76px;top:240px"><h3>Experience</h3><p>Harbourline is Australia's largest and leading providers of nationally recognised training in health administration – training from over 17 locations Australia wide.</p></div>
  <div class="point" style="left:76px;top:350px"><h3>Value</h3><p>Our innovative teaching approach allows us to deliver exceptional training at affordable prices with no hidden extras.</p></div>
  <div class="point line" style="left:628px;top:130px"><h3>Industry Recognised</h3><p>Harbourline work hand in hand with industry to develop our core programme and consolidate the programme annually to keep the programme fresh and relevant.</p></div>
  <div class="point" style="left:628px;top:240px"><h3>Great Job Results</h3><p>Harbourline students get jobs! Our focus is to create job-ready students who are mentored to achieve their goals. Harbourline also provide a recruitment service for industry and graduates.</p></div>
</section>

<section class="enquiry" role="img" aria-label="Warm orange-tinted city skyline behind the enquiry form">
  <h2 class="section-title">Make An Enquiry</h2>
  <div class="field" style="left:222px;top:148px"><svg width="12" height="12" viewBox="0 0 12 12"><circle cx="6" cy="3.5" r="3" fill="#bbb"/><path d="M0 12c0-4 12-4 12 0z" fill="#bbb"/></svg>Enter Name</div>
  <div class="field" style="left:478px;top:148px"><svg width="13" height="10" viewBox="0 0 13 10"><rect x=".5" y=".5" width="12" height="9" fill="none" stroke="#bbb"/><path d="M.5.5l6 5 6-5" fill="none" stroke="#bbb"/></svg>Enter Email</div>
  <div class="field" style="left:736px;top:148px"><svg width="12" height="12" viewBox="0 0 12 12"><rect x=".5" y="2.5" width="9" height="9" fill="none" stroke="#bbb"/><path d="M5 7l6-6" stroke="#bbb" stroke-width="1.5"/></svg>Enter Course Name</div>
  <div class="field" style="left:222px;top:210px"><svg width="12" height="12" viewBox="0 0 12 12"><circle cx="6" cy="6" r="6" fill="#bbb"/></svg>Enter State Name</div>
  <div class="field" style="left:478px;top:210px"><svg width="8" height="13" viewBox="0 0 8 13"><rect x=".5" y=".5" width="7" height="12" rx="1" fill="none" stroke="#bbb"/></svg>Enter Mobile No.</div>
  <div class="submit" style="left:736px;top:210px">SUBMIT HERE</div>
</section>

<section class="testimonials">
  <h2 class="section-title">Testimonials</h2>
  <div class="quote">I want to say a huge thank you for the course and knowledge I came away with. I have secured a fantastic job after my first application! Such good value for money too! I would highly recommend it. I'm a mature age person so it's never too late to up -skill yourself to get what you deserve!</div>
  <div class="avatar" role="img" aria-label="Portrait of the student giving the testimonial"></div>
  <span class="arrow" style="left:474px">&#8249;</span>
  <span class="client">MARA LIND</span>
  <span class="arrow" style="left:718px">&#8250;</span>
</section>

<footer class="site-footer">
  <div class="fcol" style="left:76px">
    <h4>ABOUT</h4>
    <div class="fbrand"><span></span><strong>Harbourline Institute<br>of Training</strong></div>
    <p>Lorem Ipsum is simply dummy text of the printing and typesetting industry. Lorem Ipsum has been industry's.</p>
    <div class="fsocial"><span></span><span></span><span></span><span></span></div>
  </div>
  <div class="fcol" style="left:360px">
    <h4>LATEST POSTS</h4>
    <ul>
      <li>Sed ut perspiciatis unde omn ste natus error sit voluptatem<b>JUNE 21, 2016</b></li>
      <li>Sed ut perspiciatis unde omn ste natus error sit voluptatem<b>JUNE 21, 2016</b></li>
      <li>Sed ut perspiciatis unde omn ste natus error sit voluptatem<b>JUNE 21, 2016</b></li>
    </ul>
  </div>
  <div class="fcol" style="left:633px">
    <h4>JV UPDATES</h4>
    <ul>
      <li class="tweet">"Lorem Ipsum is simply dummy text of the printing and typesetting industry. lorem Ipsum has industry's."<b>3 MONTH AGO</b></li>
      <li class="tweet">"Lorem Ipsum is simply dummy text of the printing and typesetting industry. lorem Ipsum has industry's."<b>3 MONTH AGO</b></li>
    </ul>
  </div>
  <div class="fcol" style="left:907px">
    <h4>CONTACT</h4>
    <p>41 Harbour Road, Sampletown<br>QL 4000</p>
    <p style="margin-top:12px">Call 000-000-0000<br>Email info@example.com</p>
    <h4 style="margin-top:22px;margin-bottom:10px">NEWSLETTER</h4>
    <p>By subscribing you will get the latest news form us</p>
    <div class="news"><div>Enter Email</div><b>&#8250;</b></div>
  </div>
</footer>
<div class="copyright">Copyright © 2016, Harbourline Health. All rights reserved.</div>

</body>
</html>
```